Gobal construction supply company needs new business card design

I need a business card design for my global supply company using an existing logo. i will be looking to print these on rounded corner cards with the black background version of my logo on the back. on the front white background, my logo again and my simple details.

```html
<!DOCTYPE html>
<html lang="en">
<head>
<meta charset="utf-8">
<title>Meridian Build Supply – Business Card</title>
<link rel="stylesheet" href="https://fonts.googleapis.com/css2?family=Roboto:wght@400;500;700&display=swap">
<style>
  :root {
    --backdrop: #333333;
    --card-white: #f7f7f7;
    --card-black: #1c1c1c;
    --ink: #111111;
    --text-grey: #444444;
    --rule-grey: #8a8a8a;
    --accent-red: #e00000;
    --paper-white: #ffffff;
  }
  * { margin: 0; padding: 0; box-sizing: border-box; }
  html, body { width: 1200px; height: 960px; overflow: hidden; }
  body {
    background: var(--backdrop);
    font-family: "Roboto", Arial, sans-serif;
    position: relative;
  }
  .card {
    position: absolute;
    width: 600px;
    height: 342px;
    border-radius: 20px;
    overflow: hidden;
  }
  .card-front { left: 186px; top: 113px; background: var(--card-white); }
  .card-back { left: 434px; top: 511px; background: var(--card-black); }

  .brand-front {
    position: absolute;
    left: 300px; top: 116px; width: 272px;
    text-align: center;
    font-weight: 700;
    font-size: 20px;
    line-height: 24px;
    color: var(--ink);
    white-space: nowrap;
  }

  .person-name {
    position: absolute; left: 33px; top: 164px;
    font-size: 22px; font-weight: 700; color: var(--ink);
  }
  .person-role {
    position: absolute; left: 33px; top: 188px;
    font-size: 15px; font-weight: 500; color: var(--accent-red);
  }
  .divider {
    position: absolute; left: 33px; top: 214px;
    width: 528px; height: 1px; background: var(--rule-grey);
  }
  .contact-list {
    position: absolute; left: 33px; top: 225px;
    list-style: none;
  }
  .contact-list li {
    display: flex; align-items: center;
    height: 19px;
    font-size: 14px; color: var(--text-grey);
  }
  .contact-list svg { width: 14px; height: 14px; margin-right: 9px; fill: var(--ink); }
  .address {
    position: absolute; right: 35px; top: 264px;
    text-align: right;
    font-style: normal;
    font-size: 14px; line-height: 19px; color: var(--text-grey);
  }
  .web-band {
    position: absolute; left: 301px; top: 311px;
    width: 275px; height: 31px;
    background: var(--card-black);
    clip-path: polygon(22px 0, 100% 0, 100% 100%, 0 100%);
    color: var(--paper-white);
    font-size: 14px;
    letter-spacing: 0.3px;
    display: flex; align-items: center; justify-content: flex-end;
    padding-right: 20px;
  }
  .corner-accent {
    position: absolute; left: 577px; top: 311px;
    width: 23px; height: 31px;
    background: var(--accent-red);
  }

  .brand-back {
    position: absolute;
    left: 0; top: 145px; width: 600px;
    text-align: center;
    font-weight: 700;
    font-size: 40px;
    line-height: 48px;
    color: var(--paper-white);
  }
  .web-back {
    position: absolute; left: 0; top: 290px; width: 600px;
    text-align: center;
    font-size: 14px; letter-spacing: 2.5px;
    color: var(--paper-white);
  }
</style>
</head>
<body>
  <section class="card card-front">
    <div class="brand-front">MERIDIAN BUILD SUPPLY</div>

    <div class="person-name">DANIEL HART</div>
    <div class="person-role">CEO/FOUNDER</div>
    <div class="divider"></div>

    <ul class="contact-list">
      <li>
        <svg viewBox="0 0 24 24" aria-hidden="true"><path d="M6.6 10.8a15.1 15.1 0 0 0 6.6 6.6l2.2-2.2c.3-.3.7-.4 1-.2 1.1.4 2.3.6 3.6.6.6 0 1 .4 1 1V20c0 .6-.4 1-1 1C10.6 21 3 13.4 3 4c0-.6.4-1 1-1h3.5c.6 0 1 .4 1 1 0 1.3.2 2.5.6 3.6.1.3 0 .7-.2 1z"/></svg>
        555 214 7730
      </li>
      <li>
        <svg viewBox="0 0 24 24" aria-hidden="true"><path d="M7 1h10a2 2 0 0 1 2 2v18a2 2 0 0 1-2 2H7a2 2 0 0 1-2-2V3a2 2 0 0 1 2-2zm0 3v14h10V4z"/></svg>
        555 382 6019
      </li>
      <li>
        <svg viewBox="0 0 24 24" aria-hidden="true"><path d="M6 2h12v5H6zM3 8h18a1 1 0 0 1 1 1v8h-4v5H6v-5H2V9a1 1 0 0 1 1-1zm5 8v4h8v-4z"/></svg>
        555 907 4126
      </li>
      <li>
        <svg viewBox="0 0 24 24" aria-hidden="true"><path d="M2 5h20v14H2zm2 2v.5l8 5 8-5V7l-8 5z"/></svg>
        daniel@meridianbuild.com
      </li>
    </ul>

    <address class="address">
      1240 Harbor Road<br>
      Portland, Oregon 97201
    </address>

    <div class="web-band">www.meridianbuild.com</div>
    <div class="corner-accent"></div>
  </section>

  <section class="card card-back">
    <div class="brand-back">MERIDIAN BUILD SUPPLY</div>
    <div class="web-back">www.meridianbuild.com</div>
  </section>
</body>
</html>
```